BrivoNest Learning App for Children with Dyslexia

Project Description:

We are seeking a talented UI/UX designer to create engaging and intuitive designs for Brivonest, an innovative educational app designed to help children learn letters and words through a multisensory learning approach. The app aims to be particularly helpful for children with dyslexia, providing a supportive and interactive learning environment.

Key App Features & Design Requirements:

Account Creation Screen: Design a welcoming and straightforward sign-up page that allows users to register with their email or continue with Quarnix. The design should be clean, focusing on user-friendliness and accessibility, adhering to our terms of service and privacy policy.

Main Screen Design: The main screen should allocate at least 4/6 of its height to the interactive drawing area. It needs to display word prompts in both correct and scrambled orders and include options to "Show all Words," "Play all words," and a search function. The interface should be vibrant, engaging, and easy to navigate for children.

Profile Section: Create a user-friendly profile page that allows users to edit their profile image, name, username, email, links, and bio. The design should be clean and encourage user engagement.

BrivoTally Page: This section will display the user's learning progress, including rankings, a learning curve, and recently learned words. It should visually represent progress in a motivating and understandable way, suitable for a younger audience.

Visual and Auditory Feedback Implementation: Incorporate elements that support visual and auditory feedback, using dyslexia-friendly formats. This includes choosing appropriate colors, fonts, and auditory cues.

Accessibility and Customization Settings: Designs should include settings for adjusting visual contrast, font size, and the word list to accommodate individual preferences and needs.

Feel free to add more interactions and/or pages.

Design preferences:

Color Scheme: Use a bright, inviting color palette that stimulates learning and engagement without overwhelming the users.
Font Selection: Opt for fonts that are readable and accessible, particularly for users with dyslexia.
Icons and Graphics: Design custom icons and graphics that are cohesive with the app's theme and purpose. Illustrations should be simple, relatable, and supportive of the learning process.

Target Market(s)

Educational

Industry/Entity Type

Educational

Colors
0054AA
0677BA
7BADD7
CADEEF
E8F1F8
0094D4
00A9DD
6FCCEA
C7EBF8
E9F6FB

Requirements
Must have
• Educational app, a writing area, scoring and account management
Nice to have
• Statistics, Ranking Page, Settings and some nice visual features

```html
<!DOCTYPE html>
<html lang="en">
<head>
<meta charset="utf-8">
<title>BrivoNest – App Screens</title>
<link href="https://fonts.googleapis.com/css2?family=Roboto:wght@400;500;700&display=swap" rel="stylesheet">
<style>
  :root{
    --navy:#0054AA;
    --sky:#00A9DD;
    --ink:#222428;
    --muted:#3a3d42;
    --line:#dcdcdc;
    --tile:#f2f2f2;
    --head-top:#eeeeee;
    --head-bottom:#f9f9f9;
    --white:#ffffff;
    --photo-a:#6a6a4e;
    --photo-b:#2c2a22;
  }
  *{box-sizing:border-box;margin:0;padding:0}
  html,body{width:1200px;height:847px;overflow:hidden}
  body{
    font-family:'Roboto',Arial,sans-serif;
    color:var(--ink);
    background:linear-gradient(180deg,var(--sky) 0%,#0094D4 45%,var(--navy) 100%);
    position:relative;
  }
  .screen{
    position:absolute;top:82px;width:315px;height:683px;
    background:linear-gradient(180deg,var(--head-top),var(--head-bottom) 113px);
    overflow:hidden;
  }
  .screen--signup{left:73px}
  .screen--play{left:443px}
  .screen--profile{left:812px}

  .status{position:absolute;top:14px;left:25px;right:25px;height:14px;display:flex;justify-content:space-between;align-items:center}
  .status__time{font-size:11px;font-weight:500;color:var(--ink);display:flex;align-items:center;gap:2px}
  .status__icons{display:flex;gap:3px;align-items:center}

  .brand{position:absolute;left:0;right:0;text-align:center}
  .brand__name{position:absolute;top:44px;left:0;right:0;font-size:27px;line-height:32px;font-weight:700;color:var(--sky);letter-spacing:.5px}
  .brand__tag{position:absolute;top:79px;left:0;right:0;font-size:13.5px;line-height:16px;letter-spacing:1.4px;color:var(--ink)}

  .menu-btn{position:absolute;top:57px;left:268px;width:30px;height:30px;border-radius:50%;
    background:linear-gradient(180deg,var(--sky),var(--navy));display:flex;align-items:center;justify-content:center}
  .back-btn{position:absolute;top:66px;left:19px}

  .card{position:absolute;top:113px;left:0;width:315px;height:570px;background:var(--white);border-radius:16px 16px 0 0}

  .abs{position:absolute}
  .center-text{left:0;right:0;text-align:center}
  .heading{font-size:18.5px;font-weight:700;line-height:22px;color:var(--ink)}
  .accent-bar{width:47px;height:3px;background:var(--sky);left:50%;margin-left:-23px}
  .body-text{font-size:13.5px;line-height:16px;color:var(--muted)}

  .field{position:absolute;left:19px;width:278px;height:45px;border:1px solid var(--line);background:var(--white);
    display:flex;align-items:center;padding-left:15px;font-size:13.5px;color:var(--muted)}
  .btn{position:absolute;left:19px;width:278px;height:45px;display:flex;align-items:center;justify-content:center;
    color:var(--white);font-size:13.5px;font-weight:700;letter-spacing:.1px}
  .btn--gradient{background:linear-gradient(180deg,var(--sky),var(--navy));box-shadow:0 6px 12px rgba(0,0,0,.12)}
  .btn--flat{background:var(--sky)}
  .provider{position:absolute;left:19px;width:278px;height:45px;border:1px solid var(--line);display:flex;align-items:center;justify-content:center;
    font-size:22px;font-weight:500;color:#4a4d52}
  .legal{font-size:12.5px;line-height:21px;color:var(--ink);text-align:center}
  .legal a{color:var(--sky);text-decoration:underline}

  .points{font-size:13.5px;font-weight:500;letter-spacing:.4px}
  .tools{position:absolute;left:279px;top:18px;display:flex;flex-direction:column;align-items:center;gap:7px}
  .tools svg{display:block}

  .tile{position:absolute;width:84px;height:43px;background:var(--tile);display:flex;align-items:center;justify-content:center;
    font-size:14.5px;font-weight:500;color:var(--ink)}
  .tile--more{background:var(--navy);color:var(--white)}

  .avatar{position:absolute;left:116px;width:82px;height:82px;border-radius:50%;
    background:radial-gradient(circle at 45% 40%,var(--photo-a),var(--photo-b))}
  .link-accent{color:var(--sky);font-size:14.5px;font-weight:500}
  .label{position:absolute;left:18px;font-size:13px;line-height:15px;font-weight:500;color:var(--ink);letter-spacing:.2px}
  .info{position:absolute;left:112px;width:185px;height:45px;border:1px solid var(--line);display:flex;align-items:center;justify-content:space-between;
    padding:0 14px 0 16px;font-size:13.5px;color:var(--ink)}
  .info--small{font-size:11.5px}
  .links{position:absolute;left:128px;font-size:13.5px;line-height:23.5px;color:var(--ink)}
  .links .add{color:var(--sky);font-weight:500}
</style>
</head>
<body>

<section class="screen screen--signup">
  <div class="status">
    <span class="status__time">12:00 <svg width="8" height="8" viewBox="0 0 8 8"><path d="M7 1 1 3.6l3 .6.6 3z" fill="#222"/></svg></span>
    <span class="status__icons">
      <svg width="14" height="9" viewBox="0 0 14 9"><rect x="0" y="6" width="2" height="3" fill="#222"/><rect x="3.5" y="4" width="2" height="5" fill="#222"/><rect x="7" y="2" width="2" height="7" fill="#222"/><rect x="10.5" y="0" width="2" height="9" fill="#222"/></svg>
      <svg width="12" height="9" viewBox="0 0 12 9"><path d="M1 3a7 7 0 0 1 10 0M2.8 5a4.5 4.5 0 0 1 6.4 0" stroke="#222" stroke-width="1.4" fill="none"/><circle cx="6" cy="7.5" r="1.2" fill="#222"/></svg>
      <svg width="20" height="9" viewBox="0 0 20 9"><rect x=".5" y=".5" width="17" height="8" rx="2" stroke="#222" fill="none"/><rect x="2" y="2" width="14" height="5" rx="1" fill="#222"/><rect x="18.3" y="3" width="1.4" height="3" fill="#222"/></svg>
    </span>
  </div>
  <div class="brand__name brand">BRIVONEST</div>
  <div class="brand__tag brand">Learn letters and words</div>

  <div class="card">
    <div class="abs center-text heading" style="top:81px">CREATE AN ACCOUNT</div>
    <div class="abs accent-bar" style="top:107px"></div>
    <div class="abs center-text body-text" style="top:129px">Enter your email to sign up for this app</div>
    <div class="field" style="top:181px">Enter Your Email</div>
    <div class="btn btn--gradient" style="top:239px">SIGN UP WITH EMAIL</div>
    <div class="abs center-text" style="top:320px;font-size:12px;color:var(--muted)">or continue with</div>
    <div class="provider" style="top:367px">Quarnix</div>
    <p class="abs center-text legal" style="top:440px">By clicking continue, you agree to our <a>Term of</a><br><a>Service </a> and <a>Privacy Policy</a></p>
  </div>
</section>

<section class="screen screen--play">
  <div class="status">
    <span class="status__time">12:00 <svg width="8" height="8" viewBox="0 0 8 8"><path d="M7 1 1 3.6l3 .6.6 3z" fill="#222"/></svg></span>
    <span class="status__icons">
      <svg width="14" height="9" viewBox="0 0 14 9"><rect x="0" y="6" width="2" height="3" fill="#222"/><rect x="3.5" y="4" width="2" height="5" fill="#222"/><rect x="7" y="2" width="2" height="7" fill="#222"/><rect x="10.5" y="0" width="2" height="9" fill="#222"/></svg>
      <svg width="12" height="9" viewBox="0 0 12 9"><path d="M1 3a7 7 0 0 1 10 0M2.8 5a4.5 4.5 0 0 1 6.4 0" stroke="#222" stroke-width="1.4" fill="none"/><circle cx="6" cy="7.5" r="1.2" fill="#222"/></svg>
      <svg width="20" height="9" viewBox="0 0 20 9"><rect x=".5" y=".5" width="17" height="8" rx="2" stroke="#222" fill="none"/><rect x="2" y="2" width="14" height="5" rx="1" fill="#222"/><rect x="18.3" y="3" width="1.4" height="3" fill="#222"/></svg>
    </span>
  </div>
  <div class="brand__name brand">BRIVONEST</div>
  <div class="brand__tag brand">Learn letters and words</div>
  <div class="menu-btn"><svg width="12" height="10" viewBox="0 0 12 10"><path d="M0 1h12M0 5h12M0 9h12" stroke="#fff" stroke-width="1.8"/></svg></div>

  <div class="card">
    <div class="abs center-text points" style="top:16px">16 POINTS</div>
    <div class="tools">
      <svg width="16" height="14" viewBox="0 0 16 14"><rect x=".5" y=".5" width="15" height="13" fill="none" stroke="#555"/><path d="M1 12l4-5 3 3 3-4 4 6" fill="none" stroke="#555"/><circle cx="11" cy="4" r="1.3" fill="none" stroke="#555"/></svg>
      <svg width="16" height="16" viewBox="0 0 16 16"><path d="M2 13 12 3l2 2-10 10H2zM3 2l11 11M1 5l4-4 2 2-4 4z" fill="none" stroke="#555"/></svg>
      <svg width="16" height="16" viewBox="0 0 16 16"><path d="M8 1l7 4-7 4-7-4zM1 8l7 4 7-4M1 11l7 4 7-4" fill="none" stroke="#555"/></svg>
      <svg width="16" height="16" viewBox="0 0 16 16"><rect x=".5" y="3.5" width="12" height="12" fill="none" stroke="#555"/><path d="M6 10l1-3 7-6 2 2-7 6z" fill="none" stroke="#555"/></svg>
      <svg width="18" height="12" viewBox="0 0 18 12"><path d="M1 6c4-6 12-6 16 0-4 6-12 6-16 0z" fill="none" stroke="#555"/><circle cx="9" cy="6" r="2.5" fill="none" stroke="#555"/></svg>
    </div>

    <div class="field" style="top:224px">Show All Words</div>
    <div class="btn btn--flat" style="top:281px">PLAY ALL WORDS</div>

    <div class="tile" style="left:19px;top:350px">TIME</div>
    <div class="tile" style="left:116px;top:350px">MIND</div>
    <div class="tile" style="left:212px;top:350px">TIE</div>
    <div class="tile" style="left:19px;top:406px">WIND</div>
    <div class="tile" style="left:116px;top:406px">JET</div>
    <div class="tile tile--more" style="left:212px;top:406px">MORE</div>

    <div class="btn btn--gradient" style="top:492px">SHOW ME THE RESULTS</div>
  </div>
</section>

<section class="screen screen--profile">
  <div class="status">
    <span class="status__time">12:00 <svg width="8" height="8" viewBox="0 0 8 8"><path d="M7 1 1 3.6l3 .6.6 3z" fill="#222"/></svg></span>
    <span class="status__icons">
      <svg width="14" height="9" viewBox="0 0 14 9"><rect x="0" y="6" width="2" height="3" fill="#222"/><rect x="3.5" y="4" width="2" height="5" fill="#222"/><rect x="7" y="2" width="2" height="7" fill="#222"/><rect x="10.5" y="0" width="2" height="9" fill="#222"/></svg>
      <svg width="12" height="9" viewBox="0 0 12 9"><path d="M1 3a7 7 0 0 1 10 0M2.8 5a4.5 4.5 0 0 1 6.4 0" stroke="#222" stroke-width="1.4" fill="none"/><circle cx="6" cy="7.5" r="1.2" fill="#222"/></svg>
      <svg width="20" height="9" viewBox="0 0 20 9"><rect x=".5" y=".5" width="17" height="8" rx="2" stroke="#222" fill="none"/><rect x="2" y="2" width="14" height="5" rx="1" fill="#222"/><rect x="18.3" y="3" width="1.4" height="3" fill="#222"/></svg>
    </span>
  </div>
  <svg class="back-btn" width="20" height="12" viewBox="0 0 20 12"><path d="M19 6H3M7 1 2 6l5 5" fill="none" stroke="#222" stroke-width="2.2"/></svg>
  <div class="brand__name brand">BRIVONEST</div>
  <div class="brand__tag brand">Learn letters and words</div>
  <div class="menu-btn"><svg width="12" height="10" viewBox="0 0 12 10"><path d="M0 1h12M0 5h12M0 9h12" stroke="#fff" stroke-width="1.8"/></svg></div>

  <div class="card">
    <div class="abs center-text heading" style="top:31px">PROFILE</div>
    <div class="abs accent-bar" style="top:57px;width:32px;margin-left:-16px"></div>
    <div class="avatar" style="top:81px" role="img" aria-label="Profile photo of the user"></div>
    <div class="abs center-text link-accent" style="top:179px">Edit profile image</div>

    <div class="label" style="top:234px">NAME</div>
    <div class="info" style="top:219px">Mara Quillon <svg width="7" height="11" viewBox="0 0 7 11"><path d="M1 1l4.5 4.5L1 10" fill="none" stroke="#222" stroke-width="1.6"/></svg></div>
    <div class="label" style="top:288px">USERNAME</div>
    <div class="info" style="top:273px">@username <svg width="7" height="11" viewBox="0 0 7 11"><path d="M1 1l4.5 4.5L1 10" fill="none" stroke="#222" stroke-width="1.6"/></svg></div>
    <div class="label" style="top:342px">EMAIL</div>
    <div class="info" style="top:327px">name@domain.com <svg width="7" height="11" viewBox="0 0 7 11"><path d="M1 1l4.5 4.5L1 10" fill="none" stroke="#222" stroke-width="1.6"/></svg></div>
    <div class="label" style="top:391px">LINKS</div>
    <div class="links" style="top:386px">brightpage.net<br>lettertrail.net<br>wordnook.net<br><span class="add">+ Add link</span></div>
    <div class="label" style="top:509px">BIO</div>
    <div class="info info--small" style="top:494px">A description of this user. <svg width="7" height="11" viewBox="0 0 7 11"><path d="M1 1l4.5 4.5L1 10" fill="none" stroke="#222" stroke-width="1.6"/></svg></div>
  </div>
</section>

</body>
</html>
```